Quellbrook Market Counsel needs an email sign off and professional power point template

Newly formed company and we require:1. graphic email signature on our email , and2.a professional powerpoint template (title page and sub pages) and revamp of the attached powerpoint presentation I have uploaded our business car design (logo and contact details ) and a current powerpoint template we are currently working with. Also a brief of how we operateOur mantra is Discover, Develop, Deliver.

Target Market(s)

multinationals and mid size SME's requiring help to grown new markets or geographies for their business.

Colors
000000

Requirements
Must have
• the mantra..our phases of engagement around assisting clients is:
• 1. Discover
• 2. Develop
• 3. Deliver
Nice to have
• we differentiate ourselves form consultant by actually executing the plan for them (i.e. is the delivery phase)

```html
<!DOCTYPE html>
<html lang="en">
<head>
<meta charset="utf-8">
<title>Opportunity Planning Process — Quellbrook Market Counsel</title>
<link rel="stylesheet" href="https://fonts.googleapis.com/css2?family=Oswald:wght@400;500;600;700&display=swap">
<style>
  :root {
    --ink: #000000;
    --ink-soft: #222222;
    --box: #d9d9d9;
    --paper: #ffffff;
    --divider: #cfcfcf;
    --on-dark: #ffffff;
  }
  * { box-sizing: border-box; margin: 0; padding: 0; }
  html, body { width: 1035px; height: 1200px; overflow: hidden; background: var(--paper); }
  body { font-family: "Oswald", "Arial Narrow", sans-serif; color: var(--ink-soft); }
  .canvas { position: relative; width: 1035px; height: 1200px; overflow: hidden; background: var(--paper); }

  .title {
    position: absolute; font-weight: 700; text-transform: uppercase;
    color: var(--ink); line-height: 1.1; letter-spacing: 0.5px;
  }
  .title--linear { left: 22px; top: 14px; font-size: 32px; padding-left: 8px; border-left: 4px solid var(--ink); }
  .title--cycle { left: 12px; top: 652px; font-size: 37px; }

  .top-rule { position: absolute; left: 220px; top: 0; width: 815px; height: 8px; background: var(--ink); }

  .step {
    position: absolute; display: flex; align-items: center; justify-content: center;
    text-align: center; background: var(--box); text-transform: uppercase;
    font-weight: 500; line-height: 1.2; color: var(--ink-soft);
  }
  .step--linear { font-size: 22px; padding: 8px 10px; }
  .step--cycle { font-size: 17px; padding: 6px 8px; border-radius: 12px; }

  .phase {
    position: absolute; top: 187px; width: 198px; height: 209px; background: var(--ink);
    color: var(--on-dark); display: flex; align-items: center; justify-content: center;
    font-size: 31px; font-weight: 600; text-transform: uppercase;
  }

  .arrows { position: absolute; left: 0; top: 0; width: 1035px; height: 1200px; pointer-events: none; }

  .section-divider { position: absolute; left: 0; top: 576px; width: 1035px; height: 14px; background: var(--divider); }
  .section-rule { position: absolute; top: 616px; height: 7px; background: var(--ink); }

  .mantra {
    position: absolute; left: 519px; top: 800px; width: 240px; text-align: center;
    font-size: 40px; font-weight: 700; line-height: 1.3; text-transform: uppercase; color: var(--ink);
  }

  .brand {
    position: absolute; left: 918px; top: 1112px; width: 110px;
    display: flex; flex-direction: column; align-items: center; gap: 6px;
  }
  .brand__mark { width: 42px; height: 42px; background: var(--ink-soft); }
  .brand__name { font-size: 15px; font-weight: 500; color: var(--ink-soft); }
</style>
</head>
<body>
<main class="canvas">
  <div class="top-rule"></div>
  <h1 class="title title--linear">Opportunity<br>Planning<br>Process</h1>

  <div class="step step--linear" style="left:220px;top:26px;width:132px;height:123px;">Identify<br>Opportunity</div>
  <div class="step step--linear" style="left:451px;top:26px;width:143px;height:123px;">Qualify<br>Opportunity<br>(Discover)</div>
  <div class="step step--linear" style="left:689px;top:26px;width:334px;height:123px;">Identify key individuals of influence to decision process</div>
  <div class="step step--linear" style="left:700px;top:209px;width:323px;height:143px;">Develop<br>&amp; implement sales<br>strategy &amp; plan</div>
  <div class="step step--linear" style="left:700px;top:429px;width:323px;height:132px;">Align &amp; develop<br>relationships with<br>key people of influence</div>
  <div class="step step--linear" style="left:385px;top:429px;width:209px;height:110px;">Execute plan<br>and deliver<br>proposal</div>
  <div class="step step--linear" style="left:33px;top:429px;width:253px;height:110px;">Negotiate<br>and sign</div>

  <div class="phase" style="left:33px;">Discover</div>
  <div class="phase" style="left:253px;">Develop</div>
  <div class="phase" style="left:473px;">Deliver</div>

  <div class="section-divider"></div>
  <div class="section-rule" style="left:0;width:208px;"></div>
  <div class="section-rule" style="left:238px;width:797px;"></div>

  <h2 class="title title--cycle">Opportunity<br>Planning Process</h2>

  <svg class="arrows" viewBox="0 0 1035 1200" aria-hidden="true">
    <g fill="var(--ink)">
      <rect x="363" y="80" width="52" height="16"/><polygon points="413,66 442,88 413,110"/>
      <rect x="600" y="80" width="52" height="16"/><polygon points="650,66 679,88 650,110"/>
      <rect x="839" y="154" width="16" height="26"/><polygon points="825,178 869,178 847,202"/>
      <rect x="839" y="363" width="16" height="38"/><polygon points="825,399 869,399 847,424"/>
      <rect x="632" y="486" width="56" height="16"/><polygon points="634,472 605,494 634,516"/>
      <rect x="324" y="476" width="56" height="16"/><polygon points="326,462 297,484 326,506"/>
    </g>
    <line x1="12" y1="772" x2="330" y2="772" stroke="var(--ink-soft)" stroke-width="3"/>
    <circle cx="332" cy="772" r="6" fill="var(--ink-soft)"/>
    <circle cx="640" cy="932" r="240" fill="none" stroke="var(--ink-soft)" stroke-width="14"/>
    <polygon points="520,700 552,716 522,738" fill="var(--ink-soft)"/>
  </svg>

  <div class="step step--cycle" style="left:560px;top:652px;width:165px;height:105px;">Identify<br>Opportunity</div>
  <div class="step step--cycle" style="left:761px;top:726px;width:143px;height:110px;">Qualify<br>Opportunity<br>(Discover)</div>
  <div class="step step--cycle" style="left:772px;top:858px;width:165px;height:132px;">Identify<br>key individuals of<br>influence to<br>decision process</div>
  <div class="step step--cycle" style="left:637px;top:1011px;width:165px;height:143px;">Develop<br>&amp; implement<br>sales<br>strategy &amp; plan</div>
  <div class="step step--cycle" style="left:442px;top:1001px;width:165px;height:154px;">Align &amp; develop<br>relationships<br>with<br>key people of<br>influence</div>
  <div class="step step--cycle" style="left:341px;top:858px;width:132px;height:110px;">Execute plan<br>and deliver<br>proposal</div>
  <div class="step step--cycle" style="left:363px;top:747px;width:132px;height:99px;">Negotiate<br>and sign</div>

  <div class="mantra">Discover<br>Develop<br>Deliver</div>

  <div class="brand">
    <div class="brand__mark"></div>
    <div class="brand__name">Quellbrook</div>
  </div>
</main>
</body>
</html>
```